Coffee Label Design - for university branded coffee

You will be design a new coffee pacakge, specifically a full color label for 12oz and 16oz bags.
Important: For all designs we purchase, the designers must complete the attached Copyright Transfer Agreement.pdf file and return to copyright@brewtrailpartners.com.
Please use the CoffeeLabelTemplate.ai file for proper sizing, color mode (CYMK) and resolution. The area in the golden box near the bottom MUST be left empty. All other areas can be used for your design.
A specification document is attach.
Please note we often chose 2nd and 3rd place designs, and compensate for all selected designs.
Target Market(s)
See the attached design brief
Requirements
Must have
- See the attached design brief
Nice to have

```html
<!DOCTYPE html>
<html lang="en">
<head>
<meta charset="utf-8">
<title>French Roast Coffee Label – Brew Trail Partners</title>
<link href="https://fonts.googleapis.com/css2?family=Poppins:wght@500;600&family=Oswald:wght@400&display=swap" rel="stylesheet">
<style>
  :root {
    --page-bg: #ffffff;
    --kraft-top: #b8916a;
    --kraft-bottom: #6f3f2b;
    --tan: #b8926a;
    --tan-light: #c4a07a;
    --band-dark: #521c12;
    --medallion-dark: #5a2617;
    --bean-dark: #2e170e;
    --bean-mid: #6b3a22;
    --peach: #f2caa3;
    --ink: #4a1e14;
    --flag-blue: #2a3b8f;
    --flag-white: #ffffff;
    --flag-red: #e8253f;
  }
  * { margin: 0; padding: 0; box-sizing: border-box; }
  html, body {
    width: 1200px;
    height: 960px;
    overflow: hidden;
    background: var(--page-bg);
  }
  .canvas {
    position: relative;
    width: 1200px;
    height: 960px;
  }
  .coffee-label {
    position: absolute;
    left: 384px;
    top: 40px;
    width: 432px;
    height: 880px;
    box-shadow: 0 6px 14px rgba(0,0,0,0.18);
  }
  .coffee-label svg { display: block; width: 100%; height: 100%; }
  .tab-title { font-family: "Oswald", sans-serif; font-weight: 400; fill: var(--ink); letter-spacing: 4px; }
  .brand-name { font-family: "Poppins", sans-serif; font-weight: 600; fill: var(--tan-light); }
  .product-name { font-family: "Poppins", sans-serif; font-weight: 600; fill: var(--tan); }
  .roast-level { font-family: "Poppins", sans-serif; font-weight: 600; fill: var(--tan); }
  .net-volume { font-family: "Poppins", sans-serif; font-weight: 500; fill: var(--peach); }
</style>
</head>
<body>
<main class="canvas">
  <section class="coffee-label" aria-label="French Roast coffee bag label">
    <svg viewBox="0 0 754 1535" preserveAspectRatio="none" xmlns="http://www.w3.org/2000/svg">
      <defs>
        <linearGradient id="kraftGradient" x1="0" y1="0" x2="0" y2="1">
          <stop offset="0" stop-color="var(--kraft-top)"/>
          <stop offset="1" stop-color="var(--kraft-bottom)"/>
        </linearGradient>
        <radialGradient id="beanGradient" cx="0.6" cy="0.4" r="0.8">
          <stop offset="0" stop-color="var(--bean-mid)"/>
          <stop offset="1" stop-color="var(--bean-dark)"/>
        </radialGradient>
        <filter id="softShadow" x="-20%" y="-20%" width="140%" height="140%">
          <feDropShadow dx="0" dy="4" stdDeviation="5" flood-color="#000" flood-opacity="0.35"/>
        </filter>
      </defs>

      <!-- background -->
      <rect class="label-background" width="754" height="1535" fill="url(#kraftGradient)"/>

      <!-- top tab with flag -->
      <g class="origin-tab" filter="url(#softShadow)">
        <path d="M275 0 H478 V222 Q478 240 460 240 H293 Q275 240 275 222 Z" fill="var(--kraft-top)"/>
        <path d="M275 147 H342 V240 H293 Q275 240 275 222 Z" fill="var(--flag-blue)"/>
        <rect x="342" y="147" width="68" height="93" fill="var(--flag-white)"/>
        <path d="M410 147 H478 V222 Q478 240 460 240 H410 Z" fill="var(--flag-red)"/>
      </g>
      <text class="tab-title" x="377" y="104" text-anchor="middle" font-size="46">PRIMUM</text>

      <!-- brand band -->
      <rect x="0" y="462" width="754" height="228" fill="var(--tan)"/>
      <rect x="0" y="485" width="754" height="185" fill="var(--band-dark)"/>
      <g class="brand-medallion" filter="url(#softShadow)">
        <circle cx="377" cy="577" r="197" fill="var(--tan)"/>
        <circle cx="377" cy="577" r="175" fill="var(--medallion-dark)"/>
      </g>
      <text class="brand-name" x="377" y="560" text-anchor="middle" font-size="44">Brew Trail</text>
      <text class="brand-name" x="377" y="616" text-anchor="middle" font-size="44">Partners</text>

      <!-- product name -->
      <text class="product-name" x="381" y="958" text-anchor="middle" font-size="148">FRENCH</text>
      <text class="product-name" x="389" y="1099" text-anchor="middle" font-size="148">ROAST</text>

      <!-- coffee bean area -->
      <path class="bean-border" d="M0 1430 C60 1290 220 1262 360 1302 C470 1334 520 1250 580 1130 C620 1062 700 1048 754 1062 V1535 H0 Z" fill="var(--tan)"/>
      <path class="bean-photo" role="img" aria-label="Roasted coffee beans with green coffee leaves"
            d="M0 1460 C60 1318 220 1290 360 1330 C470 1362 525 1278 585 1158 C625 1090 700 1076 754 1088 V1535 H0 Z" fill="url(#beanGradient)"/>

      <text class="roast-level" x="377" y="1233" text-anchor="middle" font-size="27">DARK ROAST</text>
      <text class="net-volume" x="377" y="1424" text-anchor="middle" font-size="38">12 Fl.oz</text>
    </svg>
  </section>
</main>
</body>
</html>
```